Brantor Works Business Card

Modern and Professional Business Card for a Med size construction/development company.

See the samples below for the design I like … but I need ideas for incorporating the red company logo while still keeping the clean look of the card samples that are attached.

Logo and tag line on the back … info on the front.

Tagline: Solid Work Built from the Base Up

Target Market(s)

Med-Large General Contractors

Contact Information for Business Card

Brantor Works Limited
42 Fenwick Avenue
Mt. Pearl, NL
A1X 0B7

t: 709-555-0147
f: 709-555-0182
w: www.brantorworks-example.com

Font styles to use
Sans Serif

Colors
fbee3e

Requirements
Must have
• I like the black and yellow designs of the attached samples …. but I'm not sure how to incorporate the red Brantor Works logo into that design??
Nice to have
• Construction safety strips

```html
<!DOCTYPE html>
<html lang="en">
<head>
<meta charset="utf-8">
<title>Brantor Works Business Card</title>
<link rel="stylesheet" href="https://fonts.googleapis.com/css2?family=Montserrat:wght@400;600;700;800&display=swap">
<style>
  :root {
    --stage: #2b2b2b;
    --card: #1c1c1c;
    --card-grain: #262626;
    --safety-yellow: #fbee3e;
    --brand-red: #d71f26;
    --ink-light: #f2f2f2;
    --ink-dark: #1a1a1a;
  }
  * { box-sizing: border-box; margin: 0; padding: 0; }
  html, body { width: 1200px; height: 1021px; overflow: hidden; }
  body {
    background: var(--stage);
    font-family: "Montserrat", sans-serif;
    position: relative;
  }
  .card {
    position: absolute;
    left: 250px;
    width: 700px;
    height: 400px;
    background: radial-gradient(ellipse at 30% 40%, var(--card-grain), var(--card) 70%);
    overflow: hidden;
    box-shadow: 0 14px 30px rgba(0,0,0,.45);
  }
  .card--back { top: 80px; }
  .card--front { top: 540px; }
  .card svg.stripes { position: absolute; inset: 0; }

  /* back: brand side */
  .brand-plate {
    position: absolute;
    left: 150px; top: 110px;
    width: 400px; height: 120px;
    display: flex; align-items: center; justify-content: center; gap: 16px;
    background: var(--card);
    white-space: nowrap;
  }
  .brand-mark {
    width: 22px; height: 22px;
    flex: none;
    background: var(--brand-red);
  }
  .brand-name {
    color: var(--ink-light);
    font-weight: 800;
    font-size: 34px;
    letter-spacing: 1px;
    text-transform: uppercase;
    line-height: 1;
  }
  .tagline {
    position: absolute;
    left: 0; right: 0; top: 290px;
    text-align: center;
    color: var(--ink-light);
    font-weight: 700;
    font-size: 21px;
    letter-spacing: .5px;
  }

  /* front: info side */
  .person {
    position: absolute;
    left: 40px; top: 148px;
    color: var(--ink-dark);
  }
  .person__name { font-weight: 700; font-size: 26px; line-height: 1.1; }
  .person__role { font-weight: 400; font-size: 16px; margin-top: 2px; }
  .address {
    position: absolute;
    left: 440px; top: 36px;
    display: flex; gap: 12px;
    color: var(--ink-light);
    font-size: 17px;
    line-height: 1.35;
  }
  .address address { font-style: normal; }
  .contact-list {
    position: absolute;
    left: 360px; top: 262px;
    list-style: none;
    color: var(--ink-light);
    font-size: 17px;
    line-height: 1.5;
    white-space: nowrap;
  }
  .contact-list li { display: flex; align-items: center; gap: 14px; }
  .icon { width: 16px; height: 16px; flex: none; }
</style>
</head>
<body>

<section class="card card--back" aria-label="Card back">
  <svg class="stripes" width="700" height="400" viewBox="0 0 700 400" aria-hidden="true">
    <g fill="var(--safety-yellow)">
      <polygon points="-20,140 30,140 0,195 -50,195"/>
      <polygon points="70,140 150,140 120,195 40,195"/>
      <polygon points="580,140 660,140 630,195 550,195"/>
      <polygon points="690,140 770,140 740,195 660,195"/>
    </g>
  </svg>
  <div class="brand-plate">
    <span class="brand-mark"></span>
    <span class="brand-name">Brantor Works</span>
  </div>
  <p class="tagline">Solid Work Built from the Base Up</p>
</section>

<section class="card card--front" aria-label="Card front">
  <svg class="stripes" width="700" height="400" viewBox="0 0 700 400" aria-hidden="true">
    <g fill="var(--safety-yellow)">
      <polygon points="0,140 330,140 300,205 0,205"/>
      <polygon points="360,140 440,140 410,205 330,205"/>
      <polygon points="470,140 550,140 520,205 440,205"/>
      <polygon points="580,140 660,140 630,205 550,205"/>
      <polygon points="690,140 770,140 740,205 660,205"/>
    </g>
  </svg>

  <div class="person">
    <p class="person__name">Daniel Fraser</p>
    <p class="person__role">Founder / Owner</p>
  </div>

  <div class="address">
    <svg class="icon" viewBox="0 0 16 16" aria-hidden="true">
      <path d="M8 1a5 5 0 0 0-5 5c0 3.6 5 9 5 9s5-5.4 5-9a5 5 0 0 0-5-5z" fill="var(--safety-yellow)"/>
      <circle cx="8" cy="6" r="2" fill="var(--card)"/>
    </svg>
    <address>
      Brantor Works Limited<br>
      42 Fenwick Avenue<br>
      Mt. Pearl, NL<br>
      A1X 0B7
    </address>
  </div>

  <ul class="contact-list">
    <li>
      <svg class="icon" viewBox="0 0 16 16" aria-hidden="true"><path d="M3 1h3l1.5 4-2 1.3a9 9 0 0 0 4.2 4.2L11 8.5l4 1.5v3a2 2 0 0 1-2 2A12 12 0 0 1 1 3a2 2 0 0 1 2-2z" fill="var(--safety-yellow)"/></svg>
      709-555-0147
    </li>
    <li>
      <svg class="icon" viewBox="0 0 16 16" aria-hidden="true"><rect x="4" y="1" width="8" height="5" fill="var(--safety-yellow)"/><rect x="1" y="6" width="14" height="6" rx="1" fill="var(--safety-yellow)"/><rect x="4" y="10" width="8" height="5" fill="var(--safety-yellow)" stroke="var(--card)"/></svg>
      709-555-0182
    </li>
    <li>
      <svg class="icon" viewBox="0 0 16 16" aria-hidden="true"><rect x="1" y="3" width="14" height="10" fill="none" stroke="var(--safety-yellow)" stroke-width="1.6"/><path d="M1 3l7 6 7-6" fill="none" stroke="var(--safety-yellow)" stroke-width="1.6"/></svg>
      info@brantorworks-example.com
    </li>
    <li>
      <svg class="icon" viewBox="0 0 16 16" aria-hidden="true"><g fill="none" stroke="var(--safety-yellow)" stroke-width="1.3"><circle cx="8" cy="8" r="6.5"/><ellipse cx="8" cy="8" rx="3" ry="6.5"/><path d="M1.5 8h13M2.5 4.5h11M2.5 11.5h11"/></g></svg>
      www.brantorworks-example.com
    </li>
  </ul>
</section>

</body>
</html>
```